GlassHaven Artbook for Okanagan Region, British Columbia

Creating an art book: GlassHaven, for the Okanagan Wine Region in British Columbia, Canada. Would like smart, modern, clean and linear...cool, sexy urban, not ugly boring suburban... I need a cover that appeals to the wino in all of us! Title: GlassHaven -Marla Dovicki
Updates
Thank you all kindly for your efforts. I have added some files so that you can get a sense of my aesthetic...it's never easy trying to figure it out, is it? I will hopefully have dimensions of book soon...cheers, Marla
would anyone please design a giant wine bottle with the wine label that looks like a label but says glasshaven...just curious to see if it works as a design or not...thank you.
Target Market(s)
Designing this wine art book of quotes to wineries in Okanagan BC. Buyer is wine lover and tourist ready to spend his vacation bucks on this wonderful book!
Look and feel

```html
<!DOCTYPE html>
<html lang="en">
<head>
<meta charset="utf-8">
<title>GlassHaven – Book Cover</title>
<link rel="stylesheet" href="https://fonts.googleapis.com/css2?family=Archivo+Black&family=Raleway:ital,wght@1,300;1,400&display=swap">
<style>
  :root {
    --page: #ffffff;
    --cover: #ebebeb;
    --maroon: #7c0615;
    --magenta: #a8005f;
    --lime: #b5d334;
    --butter: #fff68d;
    --ink: #231f20;
    --caption: #5a5a5a;
  }
  html, body {
    margin: 0;
    padding: 0;
    width: 1200px;
    height: 1200px;
    overflow: hidden;
    background: var(--page);
  }
  .canvas {
    position: relative;
    width: 1200px;
    height: 1200px;
  }
  .book-cover {
    position: absolute;
    left: 280px;
    top: 50px;
    width: 640px;
    height: 1100px;
    background: var(--cover);
  }
  .book-cover svg {
    display: block;
    width: 640px;
    height: 1100px;
  }
  .title-letter {
    font-family: "Archivo Black", "Arial Black", sans-serif;
  }
  .letter-maroon { fill: var(--maroon); }
  .letter-magenta { fill: var(--magenta); }
  .letter-lime { fill: var(--lime); }
  .letter-butter { fill: var(--butter); }
  .letter-ink { fill: var(--ink); }
  .caption {
    font-family: "Raleway", "Helvetica Neue", sans-serif;
    font-style: italic;
    font-weight: 300;
    fill: var(--caption);
  }
</style>
</head>
<body>
<main class="canvas">
  <section class="book-cover" aria-label="GlassHaven book cover">
    <svg viewBox="0 0 640 1100" xmlns="http://www.w3.org/2000/svg">
      <!-- Title, first row -->
      <g class="title-row title-row--top">
        <text class="title-letter letter-maroon" x="52" y="455" font-size="600" textLength="228" lengthAdjust="spacingAndGlyphs">G</text>
        <text class="title-letter letter-magenta" x="292" y="455" font-size="600" textLength="78" lengthAdjust="spacingAndGlyphs">L</text>
        <text class="title-letter letter-maroon" x="470" y="455" font-size="600" textLength="125" lengthAdjust="spacingAndGlyphs">A</text>
      </g>

      <!-- Title, second row -->
      <g class="title-row title-row--middle">
        <text class="title-letter letter-lime" x="52" y="850" font-size="515" textLength="270" lengthAdjust="spacingAndGlyphs">S</text>
        <text class="title-letter letter-butter" x="330" y="850" font-size="515" textLength="265" lengthAdjust="spacingAndGlyphs">S</text>
      </g>

      <!-- Title, closing word -->
      <text class="title-letter letter-ink title-row--bottom" x="52" y="1080" font-size="320" textLength="543" lengthAdjust="spacingAndGlyphs">HAVEN</text>

      <!-- Author, set vertically -->
      <g class="author" transform="translate(36 470) rotate(-90)">
        <text class="caption" x="0" y="0" font-size="22" letter-spacing="2">Marla</text>
        <text class="caption" x="0" y="24" font-size="22" letter-spacing="2">Dovicki</text>
      </g>

      <!-- Region subtitle -->
      <g class="region">
        <text class="caption" x="462" y="420" font-size="17" text-anchor="end">Okanagan</text>
        <text class="caption" x="462" y="442" font-size="17" text-anchor="end">Wine Region</text>
      </g>
    </svg>
  </section>
</main>
</body>
</html>
```